home accents e-commerce website

I'd like a professional simple website designed where I can sell my home goods. I already have my domain name registered. I need the website to accept credit card payments and Monvex. It should have a shopping cart option and calculate sales tax and shipping costs on merchandise automatically.

I'll be taking photographs of the merchandise and writing product descriptions myself. (I'm not a professional photographer, so these photos probably won't look too polished. If you can help me make them look better, that'd be great). As I add new merchandise in the future, I'd like an option where I can log in to the back end myself and add pictures/product descriptions. And take old products down as they sell out. So the website needs to be user-friendly for me, even though I'm completely web design illiterate!

I'd like a creative, talented person who can create a whimsical, cute website. Nothing too corporate-looking.

Thank you!

Target Market(s)

women, online shoppers, New York City-area, (ship products to the United States only)

Industry/Entity Type

Home And Garden

Coding

Coded - Design and coding required

Number of Pages Required

1 page

Font styles to use
Sans Serif

Colors
0355a3
ffffff

Requirements
Must have
• shopping cart feature
• safe, secure credit card and Monvex payments
• ability for me to go in and add new products and take down old/sold products
Nice to have
• whimsical, cute design
Should not have
• too corporate-looking

```html
<!DOCTYPE html>
<html lang="en">
<head>
<meta charset="utf-8">
<title>Lumora Home Goods</title>
<link rel="stylesheet" href="https://fonts.googleapis.com/css2?family=Open+Sans:wght@400;600;700&family=Roboto:wght@400;500;700&display=swap">
<style>
:root{
  --brand:#0355a3;
  --white:#ffffff;
  --ink:#333333;
  --muted:#777777;
  --nav:#4a4a4a;
  --footer:#343434;
  --soft:#efefef;
  --line:#dddddd;
  --btn-grey:#b9b9b9;
}
*{box-sizing:border-box;margin:0;padding:0}
html,body{width:1200px;height:2667px;overflow:hidden;background:var(--white)}
body{position:relative;font-family:"Open Sans",Arial,sans-serif;color:var(--ink)}
h1,h2,h3,h4{font-family:"Roboto",Arial,sans-serif;font-weight:500}

/* header */
.site-header{position:absolute;left:0;top:0;width:1200px;height:125px}
.brand{position:absolute;left:100px;top:26px;color:var(--brand);font-family:"Roboto",sans-serif;font-weight:700}
.brand-name{font-size:50px;line-height:48px;letter-spacing:1px}
.brand-tag{font-size:14px;letter-spacing:6px;font-weight:400;color:var(--brand)}
.cart{position:absolute;left:725px;top:44px;display:flex;align-items:center;gap:12px;font-size:16px;font-family:"Roboto",sans-serif}
.cart b{color:var(--brand);font-weight:500}
.social{position:absolute;left:920px;top:40px;display:flex;gap:10px}
.social span{width:38px;height:38px;border-radius:50%;display:block}
.social span:nth-child(1){background:#3b5b98}
.social span:nth-child(2){background:#3a3a3a}
.social span:nth-child(3){background:#c8232c}
.social span:nth-child(4){background:#1da1f2}

.main-nav{position:absolute;left:0;top:125px;width:1200px;height:60px;background:var(--nav);display:flex}
.main-nav a{color:var(--white);text-decoration:none;font-family:"Roboto",sans-serif;font-size:19px;display:flex;align-items:center;justify-content:center}
.main-nav a:nth-child(1){width:413px;border-right:2px solid #eee}
.main-nav a:nth-child(2){width:373px;background:var(--brand);border-right:2px solid #eee}
.main-nav a:nth-child(3){width:314px}

/* hero */
.hero{position:absolute;left:0;top:185px;width:1200px;height:515px;background:linear-gradient(90deg,#d0cdc8 0%,#c5c3c0 55%,#bdbcbb 100%)}
.hero-media{position:absolute;left:25px;top:40px;width:680px;height:445px;border-radius:40px;background:radial-gradient(ellipse at 50% 55%,#d46a3a 0%,#c98a3a 30%,#7fae6a 55%,#b93b3b 70%,rgba(200,198,195,0) 90%)}
.hero-brand{position:absolute;right:100px;top:45px;text-align:right;color:var(--brand);font-family:"Roboto",sans-serif;font-weight:700}
.hero-brand .brand-name{font-size:84px;line-height:84px}
.hero-brand .brand-tag{font-size:25px;letter-spacing:9px;font-weight:400}
.hero-copy{position:absolute;right:100px;top:225px;width:460px;text-align:right;color:var(--white);font-size:18px;line-height:31px;font-weight:600}
.hero-btn{position:absolute;left:968px;top:323px;width:132px;height:54px;border:2px solid var(--white);color:var(--white);font-size:16px;display:flex;align-items:center;justify-content:center}
.hero-dots{position:absolute;left:1006px;top:413px;display:flex;gap:5px}
.hero-dots i{width:14px;height:14px;border-radius:50%;background:#d9d9d9;display:block}
.hero-dots i:first-child{background:var(--white)}

/* sidebar */
.categories{position:absolute;left:100px;top:760px;width:262px;height:426px;border:1px solid var(--line);background:#f7f7f7}
.panel-head{background:var(--brand);color:var(--white);height:62px;display:flex;align-items:center;font-family:"Roboto",sans-serif;font-size:22px}
.categories .panel-head{justify-content:center;margin:-1px -1px 0}
.cat-list{list-style:none;padding:14px 14px 0 14px}
.cat-list li{height:36px;display:flex;align-items:center;font-size:15px;color:#444}
.cat-list li::before{content:"";width:12px;height:12px;border-radius:50%;background:var(--brand);margin-right:14px}
.cat-list li span{flex:1}
.cat-list li em{width:18px;height:18px;border:1px solid #777;border-radius:50%;display:block}
.room-promo{position:absolute;left:100px;top:1222px;width:262px;height:418px;background:linear-gradient(180deg,#8d8b88 0%,#6f6b66 48%,#c6472f 62%,#e0b33b 78%,#3c7ec2 100%)}

/* products */
.products-head{position:absolute;left:392px;top:760px;width:710px;height:60px;padding-left:16px;justify-content:space-between}
.search{width:232px;height:40px;border:2px solid var(--white);margin-right:16px;display:flex;align-items:center;justify-content:space-between;padding:0 12px;font-size:16px;font-family:"Open Sans",sans-serif}
.product{position:absolute;width:214px;height:323px;border:1px solid var(--line);background:var(--white);box-shadow:0 10px 8px -8px rgba(0,0,0,.2)}
.product-img{margin:8px;height:185px}
.product h3{font-size:14px;text-align:center;margin-top:14px;font-weight:400;color:#222}
.price-row{display:flex;align-items:center;padding:0 14px;margin-top:14px;font-size:14px}
.price-row .price{flex:1}
.price-row i{width:22px;height:22px;border:1px solid #888;border-radius:50%;margin-left:16px;display:block}
.buy{position:absolute;left:0;right:0;bottom:0;height:38px;background:var(--btn-grey);color:var(--white);font-family:"Roboto",sans-serif;font-size:16px;font-weight:500;display:flex;align-items:center;justify-content:center}
.product.active .buy{background:var(--brand)}
.product.active .price{color:var(--brand)}
.pager{position:absolute;left:392px;top:1590px;width:710px;height:50px;border:1px solid var(--line);background:#fafafa;display:flex;align-items:center;justify-content:flex-end;gap:16px;padding-right:18px;font-size:14px}
.pager b{width:32px;height:30px;border:1px solid #bbb;display:flex;align-items:center;justify-content:center;font-weight:400}
.pager b.on{background:var(--brand);color:var(--white);border-color:var(--brand)}

/* blog */
.blog{position:absolute;left:0;top:1712px;width:1200px;height:508px;background:var(--soft)}
.blog h2{position:absolute;top:50px;width:100%;text-align:center;color:var(--brand);font-size:27px;font-weight:700}
.blog-intro{position:absolute;top:106px;width:100%;text-align:center;color:var(--muted);font-size:14px}
.post{position:absolute;width:460px}
.post-thumb{position:absolute;left:0;top:0;width:104px;height:104px;border-radius:50%;border:4px solid #ddd}
.post-body{position:absolute;left:130px;top:0;width:330px}
.post h4{font-size:17px;color:#222;margin-bottom:8px}
.post p{font-size:12px;line-height:16px;color:#555}
.post a{display:block;margin-top:8px;color:var(--brand);font-size:12px;text-decoration:none}

/* footer */
.site-footer{position:absolute;left:0;top:2220px;width:1200px;height:447px;background:var(--footer);color:var(--white)}
.fcol{position:absolute;top:62px}
.fcol h4{font-size:17px;font-weight:500;margin-bottom:34px;position:relative}
.fcol h4::after{content:"";position:absolute;left:0;bottom:-10px;width:60px;height:2px;background:#999}
.flinks{list-style:none}
.flinks li{font-size:13px;height:28px;display:flex;align-items:center}
.flinks li::before{content:"";width:11px;height:11px;border-radius:50%;background:var(--white);margin-right:14px}
.follow{display:flex;gap:8px}
.follow i{width:30px;height:30px;border:2px solid var(--white);border-radius:50%;display:block}
.pay{display:flex;gap:6px}
.pay span{width:44px;height:26px;background:var(--white);color:var(--brand);font-size:9px;font-weight:700;display:flex;align-items:center;justify-content:center}
.news p{font-size:13px;line-height:20px;width:232px;text-align:justify}
.news .field{margin-top:12px;width:232px;height:38px;background:var(--white);color:#999;font-size:13px;padding:0 10px;display:flex;align-items:center}
.news .sub{margin-top:12px;width:106px;height:40px;background:var(--brand);border:2px solid var(--white);font-size:13px;display:flex;align-items:center;justify-content:center}
.footer-rule{position:absolute;left:98px;top:382px;width:1004px;height:1px;background:#777}
.copyright{position:absolute;top:405px;width:100%;text-align:center;font-size:15px}
</style>
</head>
<body>

<header class="site-header">
  <div class="brand"><div class="brand-name">lumora</div><div class="brand-tag">HOME GOODS</div></div>
  <div class="cart">
    <svg width="34" height="34" viewBox="0 0 34 34"><circle cx="17" cy="17" r="17" fill="#0355a3"/><path d="M9 11h3l2 9h9l2-6H13" fill="none" stroke="#fff" stroke-width="2"/><circle cx="15" cy="23" r="1.6" fill="#fff"/><circle cx="22" cy="23" r="1.6" fill="#fff"/></svg>
    <span><b>CART:</b> 0 Items</span>
  </div>
  <div class="social" aria-label="Social links"><span></span><span></span><span></span><span></span></div>
</header>

<nav class="main-nav">
  <a href="#">ABOUT LUMORA</a>
  <a href="#">HOW DOES THIS CRAZINESS WORK?</a>
  <a href="#">CONTACT</a>
</nav>

<section class="hero">
  <div class="hero-media" role="img" aria-label="Stack of rolled colourful wool throw blankets"></div>
  <div class="hero-brand"><div class="brand-name">lumora</div><div class="brand-tag">HOME GOODS</div></div>
  <p class="hero-copy">Nemo enim ipsam voluptatem quia voluptas sit aspernatur aut odit aut fugit, sed quias</p>
  <div class="hero-btn">READ MORE</div>
  <div class="hero-dots"><i></i><i></i><i></i><i></i><i></i></div>
</section>

<aside class="categories">
  <div class="panel-head">CATEGORIES</div>
  <ul class="cat-list">
    <li><span>Vases</span><em></em></li>
    <li><span>Throw Pillows</span><em></em></li>
    <li><span>Blankets and Throws</span><em></em></li>
    <li><span>For Your Floors</span><em></em></li>
    <li><span>For Your Walls</span><em></em></li>
    <li><span>For Your Table</span><em></em></li>
    <li><span>For Your Bedside</span><em></em></li>
    <li><span>Let THere Be Light</span><em></em></li>
    <li><span>Put Your Feet Up</span><em></em></li>
  </ul>
</aside>
<div class="room-promo" role="img" aria-label="Living room with grey sofa and striped rainbow rug, brand name on the wall"></div>

<div class="panel-head products-head">OUR PRODUCTS
  <div class="search"><span>Search</span><svg width="14" height="14" viewBox="0 0 14 14"><circle cx="6" cy="6" r="4.5" fill="none" stroke="#fff" stroke-width="2"/><path d="M9.5 9.5L13 13" stroke="#fff" stroke-width="2"/></svg></div>
</div>

<div class="product" style="left:392px;top:857px">
  <div class="product-img" role="img" aria-label="Pink peonies in a teal glass vase" style="background:linear-gradient(180deg,#e9e2d8,#c9b8a6)"></div>
  <h3>VASES</h3><div class="price-row"><span class="price">$150.00</span><i></i><i></i><i></i></div><div class="buy">BUY NOW</div>
</div>
<div class="product active" style="left:638px;top:857px">
  <div class="product-img" role="img" aria-label="Red and white roses in a clear glass vase" style="background:linear-gradient(180deg,#c0455a,#d9d4d2)"></div>
  <h3>VASES</h3><div class="price-row"><span class="price">$150.00</span><i></i><i></i><i></i></div><div class="buy">BUY NOW</div>
</div>
<div class="product" style="left:885px;top:857px">
  <div class="product-img" role="img" aria-label="Stack of orange, red and green throw pillows" style="background:radial-gradient(circle,#e2522e 0%,#f1a25a 40%,#fff 72%)"></div>
  <h3>THROW PILLOWS</h3><div class="price-row"><span class="price">$50.00</span><i></i><i></i><i></i></div><div class="buy">BUY NOW</div>
</div>
<div class="product" style="left:392px;top:1212px">
  <div class="product-img" role="img" aria-label="Folded purple knitted blanket" style="background:radial-gradient(circle,#7a63c8 0%,#9c8bdb 40%,#fff 72%)"></div>
  <h3>BLANKETS AND THROWS</h3><div class="price-row"><span class="price">$90.00</span><i></i><i></i><i></i></div><div class="buy">BUY NOW</div>
</div>
<div class="product" style="left:638px;top:1212px">
  <div class="product-img" role="img" aria-label="Stack of brightly coloured folded table linens" style="background:radial-gradient(circle,#e8347a 0%,#3aa0d8 35%,#f2b93a 50%,#fff 72%)"></div>
  <h3>FOR YOUR TABLE</h3><div class="price-row"><span class="price">$350.00</span><i></i><i></i><i></i></div><div class="buy">BUY NOW</div>
</div>
<div class="product" style="left:885px;top:1212px">
  <div class="product-img" role="img" aria-label="Red and black check throw on a white bed" style="background:linear-gradient(160deg,#e6e3e0 20%,#a3202c 55%,#2b1a1c 100%)"></div>
  <h3>FOR YOUR BEDSIDE</h3><div class="price-row"><span class="price">$50.00</span><i></i><i></i><i></i></div><div class="buy">BUY NOW</div>
</div>

<div class="pager"><span>&lt;&lt; Before</span><b>1</b><b class="on">2</b><b>3</b><b>4</b><span>Next &gt;&gt;</span></div>

<section class="blog">
  <h2>OUR BLOG</h2>
  <p class="blog-intro">Donec quam felis, ultricies nec, pellentesque&nbsp; pretium quis sem. Nulla consequat massa quis enim</p>
  <article class="post" style="left:100px;top:173px">
    <div class="post-thumb" role="img" aria-label="Cushions on a sofa" style="background:radial-gradient(circle,#b3473f,#e8dcd2)"></div>
    <div class="post-body"><h4>Nemo enim ipsam voluptatem</h4><p>Lorem ipsum dolor sit amet, consetetur sadipscing elitr, sed diam nonumy invilut labore diam nonumy consetetur sadipscing elitr nonumy invilut labore</p><a href="#">Read More</a></div>
  </article>
  <article class="post" style="left:640px;top:173px">
    <div class="post-thumb" role="img" aria-label="Wooden bench with cushions" style="background:radial-gradient(circle,#8a7a62,#cfc6b8)"></div>
    <div class="post-body"><h4>Quasi architecto beatae</h4><p>Lorem ipsum dolor sit amet, consetetur sadipscing elitr, sed diam nonumy invilut labore diam nonumy consetetur sadipscing elitr nonumy invilut labore</p><a href="#">Read More</a></div>
  </article>
  <article class="post" style="left:100px;top:328px">
    <div class="post-thumb" role="img" aria-label="Grey sofa with pink pillows" style="background:radial-gradient(circle,#9a9a9a,#e7c3cf)"></div>
    <div class="post-body"><h4>Exercitation ullamco laboris</h4><p>Lorem ipsum dolor sit amet, consetetur sadipscing elitr, sed diam nonumy invilut labore diam nonumy consetetur sadipscing elitr nonumy invilut labore</p><a href="#">Read More</a></div>
  </article>
  <article class="post" style="left:640px;top:328px">
    <div class="post-thumb" role="img" aria-label="Lilac flowers in a jar" style="background:radial-gradient(circle,#b79bd0,#ece7e2)"></div>
    <div class="post-body"><h4>Commodo consequat</h4><p>Lorem ipsum dolor sit amet, consetetur sadipscing elitr, sed diam nonumy invilut labore diam nonumy consetetur sadipscing elitr nonumy invilut labore</p><a href="#">Read More</a></div>
  </article>
</section>

<footer class="site-footer">
  <div class="fcol" style="left:98px"><h4>SUPPORT</h4>
    <ul class="flinks"><li>Contact Us</li><li>Shopping Cart</li><li>Faq</li><li>Careers</li><li>Shipping</li><li>Returns</li></ul></div>
  <div class="fcol" style="left:355px"><h4>POPULAR LINKS</h4>
    <ul class="flinks"><li>Vases</li><li>Throw Pillows</li><li>Blankets and Throws</li><li>For Your Floors</li><li>For Your Walls</li><li>For Your Table</li><li>For Your Bedside</li></ul></div>
  <div class="fcol" style="left:594px"><h4>FOLLOW US</h4>
    <div class="follow"><i></i><i></i><i></i><i></i></div>
    <h4 style="margin-top:26px;margin-bottom:30px">WE ACCEPT</h4>
    <div class="pay"><span>Monvex</span><span>Cardiva</span><span>Orbcard</span></div></div>
  <div class="fcol news" style="left:868px"><h4>NEWSLETTER</h4>
    <p>Subscribe and be the first to hear news, offers and updates for the lumora community!</p>
    <div class="field">Your Email</div><div class="sub">SUBSCRIBE</div></div>
  <div class="footer-rule"></div>
  <p class="copyright">Copyrights @ 2017. Lumora. All rights reserved</p>
</footer>

</body>
</html>
```